Hop Along Days campaign: promoting kids play in the UK - Website Redesign

Hop Along Days is a national UK campaign that promotes the value of play for children. The current website is live at http://www.hopalongdays.co.uk. This website has been live for 4 years and now needs to be redesigned. The target audience is parents of young children up to the age of 12.

The current site was designed with a series of old adverts in mind. Here is an example of an old advert: http://vidshare.example/qR7tLm2XwZa

Criticisms of existing site:
The design represented the adverts too closely. The result was a website that mirrors the adverts rather than complements them.
The color scheme is too dark.
Text-heavy pages (e.g. http://www.hopalongdays.co.uk/fun.php) are dull and not FUN!

New site
We have recently had a series of new video adverts produced:
advert 1: http://vidshare.example/hB4nVc8JsPe
advert 2: http://vidshare.example/KgW3rTy9DuM
advert 3: http://vidshare.example/zA5oEi1HbNq

The new site should be cleaner and brighter than the existing site, possibly with a white background using graphics, fonts and advert characters (see attached character graphics files) to add the element of fun and play.

The homepage should include:
1. Hop Along Days logo (attached)
2. Social Media links (visible on all pages of the site) – Chatterbook, Chirpline, ClipVault
3. Link to the HopAlongDays app page of the site (visible on all pages)
4. Image/video placeholder that the user can scroll through, view full-size images and play videos.
5. Text area to hold approximately 100 words describing the purpose of the campaign
6. Site footer to contain the same information as on the existing site along with the Northern Games & Crafts Guild logo (attached)

Site structure:
One change to the site structure… the “Brought to you by” menu item will be removed from the top-level menu.

General:
Some pages on the existing site are quite text-heavy, we would like to break up text on these pages in some way. Graphical division of paragraphs, use of advert characters?

Please note that all attached graphics file are the property of the Northern Games & Crafts Guild and must only be used for the purpose of this project.

```html
<!DOCTYPE html>
<html lang="en">
<head>
<meta charset="utf-8">
<title>Hop Along Days</title>
<link href="https://fonts.googleapis.com/css2?family=Open+Sans:wght@400;600&family=Crimson+Text:ital,wght@1,600&display=swap" rel="stylesheet">
<style>
  :root {
    --cream: #fdf9ea;
    --cloud: #f3d488;
    --ink: #1f1f1f;
    --body: #333333;
    --rule: #efe6c8;
    --card: #f8f8f6;
    --card-line: #e2e2de;
    --link: #3a9ad9;
    --pink: #d93c6a;
    --nav-gold: #e6b43a;
    --nav-purple: #6a40a3;
    --nav-blue: #58ace2;
    --nav-green: #a6c43f;
    --nav-yellow: #e8cd36;
    --nav-rose: #cc5175;
    --btn-dark: #474747;
    --grass-top: #a9d25a;
    --grass-low: #5f9d2b;
    --sky: #bfe3f2;
    --hill: #9cc94c;
  }
  * { box-sizing: border-box; margin: 0; padding: 0; }
  html, body { width: 840px; height: 1200px; overflow: hidden; }
  body {
    position: relative;
    background: var(--cream);
    font-family: "Open Sans", Arial, sans-serif;
    color: var(--body);
  }
  a { text-decoration: none; }
  .abs { position: absolute; }
  .cloud-band { left: 0; top: 0; width: 840px; height: 70px; }

  .brand { left: 126px; top: 76px; display: flex; align-items: center; gap: 8px; }
  .brand-dot { width: 22px; height: 22px; border-radius: 50%; background: var(--nav-purple); }
  .brand-name { font-weight: 600; font-size: 24px; color: var(--nav-purple); }

  .social { left: 636px; top: 96px; display: flex; gap: 5px; list-style: none; }
  .social a { display: block; width: 23px; height: 23px; border-radius: 4px; }
  .social .chirpline { background: var(--nav-blue); }
  .social .clipvault { background: #d9342b; }
  .social .chatterbook { background: #3d5a98; }
  .sr { position: absolute; width: 1px; height: 1px; overflow: hidden; clip: rect(0 0 0 0); }

  .main-nav { left: 126px; top: 139px; width: 588px; height: 37px; }
  .main-nav a {
    position: absolute; top: 0; height: 37px; border-radius: 2px;
    display: flex; align-items: center; justify-content: center; white-space: nowrap;
    font-family: "Crimson Text", Georgia, serif; font-style: italic; font-weight: 600;
    font-size: 13px; color: #fff;
  }

  .hero { left: 126px; top: 188px; width: 588px; height: 264px; border-radius: 10px; overflow: hidden;
    background: linear-gradient(180deg, var(--sky) 0%, #d6edf5 30%, var(--hill) 55%, #7fb83a 100%);
    box-shadow: 0 4px 6px rgba(0,0,0,.12); border: 4px solid #fff; }
  .hero-arrow { width: 22px; height: 22px; top: 132px; }

  .section-title { font-size: 16px; font-weight: 400; color: var(--ink); }
  .section-title b { font-weight: 600; }
  .welcome-title { left: 126px; top: 469px; }
  .news-title { left: 426px; top: 469px; }
  .news-title span { color: var(--pink); }
  .rule { height: 1px; background: var(--rule); top: 502px; }

  .feature-media { left: 126px; top: 520px; width: 273px; height: 130px;
    background: linear-gradient(180deg, #e9b43a 0%, #bfe0ea 35%, #8cbf52 100%); }
  .play-btn { left: 50%; top: 50%; width: 30px; height: 30px; margin: -15px 0 0 -15px; }

  .purpose-title { left: 126px; top: 664px; font-size: 15px; font-weight: 400; color: var(--ink); }
  .purpose-text { left: 126px; top: 693px; width: 274px; font-size: 7.1px; line-height: 13.2px; color: var(--body); }
  .learn-more { left: 128px; top: 770px; width: 68px; height: 26px; background: var(--btn-dark); color: #fff;
    border-radius: 2px; font-size: 8.5px; font-weight: 600; display: flex; align-items: center; justify-content: center; }

  .news-card { left: 426px; width: 288px; height: 130px; background: var(--card); border: 1px solid var(--card-line); }
  .news-thumb { left: 13px; top: 15px; width: 94px; height: 91px; border-radius: 10px; border: 3px solid #fff;
    background: linear-gradient(180deg, #8fcbe8 0%, #cfe8f0 50%, #8ec54d 100%); box-shadow: 0 1px 3px rgba(0,0,0,.15); }
  .news-head { left: 122px; top: 13px; font-size: 11px; font-weight: 400; color: var(--ink); }
  .news-date { left: 122px; top: 37px; font-size: 7px; color: var(--body); }
  .news-text { left: 122px; top: 54px; width: 153px; font-size: 7px; line-height: 13.2px; text-align: justify; color: var(--body); }
  .read-more { right: 14px; top: 110px; font-size: 7px; color: var(--link); }

  .video-tile { top: 818px; width: 184px; height: 136px; border: 1px solid #6b6b6b; overflow: hidden; }
  .video-tile .still { width: 100%; height: 100%; }
  .video-bar { left: 0; bottom: 0; width: 100%; height: 14px; background: rgba(20,20,20,.85); }
  .video-bar .track { left: 26px; top: 6px; width: 100px; height: 2px; background: #666; }
  .video-bar .track i { position: absolute; left: 0; top: 0; width: 40px; height: 2px; background: #3a8fd0; }

  .footer-scene { left: 0; top: 960px; width: 840px; height: 240px; }
  .footer-links { left: 0; top: 978px; width: 840px; text-align: center; font-size: 7.5px; color: var(--body); }
  .footer-links a { color: var(--body); }
  .footer-links .sep { margin: 0 4px; }
  .copyright { left: 0; top: 1007px; width: 840px; text-align: center; font-size: 7.5px; color: var(--body); }
  .guild { left: 300px; top: 1134px; width: 240px; display: flex; flex-direction: column; align-items: center; gap: 5px; }
  .guild-mark { width: 22px; height: 22px; border-radius: 50%; background: #e6b43a; }
  .guild-name { font-size: 8px; font-weight: 600; color: #fff; white-space: nowrap; }
</style>
</head>
<body>
  <svg class="abs cloud-band" viewBox="0 0 840 70" aria-hidden="true">
    <path d="M0 0H840V40C820 52 800 38 780 46C760 60 735 44 715 52C690 64 665 46 640 54C610 66 585 48 560 56C530 66 505 50 480 58C455 66 430 50 405 56C380 66 355 50 330 56C300 64 275 48 250 54C225 62 200 46 175 52C150 60 125 44 100 50C75 58 50 42 25 48C15 50 5 46 0 44Z" fill="var(--cloud)"/>
  </svg>

  <header>
    <a class="abs brand" href="#"><span class="brand-dot"></span><span class="brand-name">Hop Along Days</span></a>
    <ul class="abs social">
      <li><a class="chirpline" href="#"><span class="sr">Chirpline</span></a></li>
      <li><a class="clipvault" href="#"><span class="sr">ClipVault</span></a></li>
      <li><a class="chatterbook" href="#"><span class="sr">Chatterbook</span></a></li>
    </ul>
    <nav class="abs main-nav">
      <a href="#" style="left:0;width:100px;background:var(--nav-gold)">Play Right Now</a>
      <a href="#" style="left:108px;width:93px;background:var(--nav-purple)">Get Involved</a>
      <a href="#" style="left:211px;width:74px;background:var(--nav-blue)">Why Play</a>
      <a href="#" style="left:295px;width:86px;background:var(--nav-green)">Fun Forever</a>
      <a href="#" style="left:392px;width:108px;background:var(--nav-yellow)">HopAlongDays App</a>
      <a href="#" style="left:509px;width:79px;background:var(--nav-rose)">Resources</a>
    </nav>
  </header>

  <section class="abs hero" role="img" aria-label="Slideshow illustration of three children standing in green hills with trees and a rainbow, campaign title above">
    <svg class="abs hero-arrow" style="left:36px" viewBox="0 0 22 22" aria-hidden="true"><circle cx="11" cy="11" r="10" fill="#fff" opacity=".85"/><path d="M13 6L8 11L13 16" stroke="#666" stroke-width="2" fill="none"/></svg>
    <svg class="abs hero-arrow" style="left:542px" viewBox="0 0 22 22" aria-hidden="true"><circle cx="11" cy="11" r="10" fill="#fff" opacity=".85"/><path d="M9 6L14 11L9 16" stroke="#666" stroke-width="2" fill="none"/></svg>
  </section>

  <main>
    <h2 class="abs section-title welcome-title">Welcome To <b>HopAlongDays</b></h2>
    <div class="abs rule" style="left:126px;width:274px"></div>
    <h2 class="abs section-title news-title">News &amp; <span>Events</span></h2>
    <div class="abs rule" style="left:426px;width:288px"></div>

    <div class="abs feature-media" role="img" aria-label="Video still of two children playing by a big tree">
      <svg class="abs play-btn" viewBox="0 0 30 30" aria-hidden="true"><circle cx="15" cy="15" r="13" fill="rgba(255,255,255,.35)" stroke="#fff" stroke-width="2"/><path d="M12 9L21 15L12 21Z" fill="#fff"/></svg>
    </div>

    <h3 class="abs purpose-title">Purpose of The Campaign</h3>
    <p class="abs purpose-text">Aenean placerat tortor ac dui luctus ut mattis est mollis. Donec blandit orci id velit cursus varius. Fusce quam enim, hendrerit nec ultrices a, vestibulum nec enim. Quisque imperdiet ultricies dolor in convallis. Morbi sed fringilla elit. Duis sagittis lectus in orci volutpat elementum. Cras in purus sem. Curabitur augue velit, mollis in suscipit eleifend, faucibus ac elit. Morbi mattis tristique mi,</p>
    <a class="abs learn-more" href="#">Learn More</a>

    <article class="abs news-card" style="top:520px">
      <div class="abs news-thumb" role="img" aria-label="Illustration of children holding balloons"></div>
      <h4 class="abs news-head">Quis Nostrum</h4>
      <p class="abs news-date">March-22-2011</p>
      <p class="abs news-text">Lorem ipsum dolor sit amet, consectetuer adipiscing elit, sed diam nonummy nibh euismod tincidunt ut laoreet dolore magna aliquam erat volutpat.</p>
      <a class="abs read-more" href="#">Read More</a>
    </article>
    <article class="abs news-card" style="top:667px">
      <div class="abs news-thumb" role="img" aria-label="Illustration of children holding balloons"></div>
      <h4 class="abs news-head">Quis Nostrum</h4>
      <p class="abs news-date">March-22-2011</p>
      <p class="abs news-text">Lorem ipsum dolor sit amet, consectetuer adipiscing elit, sed diam nonummy nibh euismod tincidunt ut laoreet dolore magna aliquam erat volutpat.</p>
      <a class="abs read-more" href="#">Read More</a>
    </article>

    <div class="abs video-tile" style="left:126px">
      <div class="still" role="img" aria-label="Advert video still of a cardboard playroom" style="background:linear-gradient(160deg,#c99a45,#7a5a2e)"></div>
      <svg class="abs play-btn" viewBox="0 0 30 30" aria-hidden="true"><circle cx="15" cy="15" r="13" fill="rgba(255,255,255,.3)" stroke="#fff" stroke-width="2"/><path d="M12 9L21 15L12 21Z" fill="#fff"/></svg>
      <div class="abs video-bar"><div class="abs track"><i></i></div></div>
    </div>
    <div class="abs video-tile" style="left:329px">
      <div class="still" role="img" aria-label="Advert video still of children dressing up on a stage" style="background:linear-gradient(160deg,#e9e2d2,#b64a45 60%,#cfc6b4)"></div>
      <svg class="abs play-btn" viewBox="0 0 30 30" aria-hidden="true"><circle cx="15" cy="15" r="13" fill="rgba(255,255,255,.3)" stroke="#fff" stroke-width="2"/><path d="M12 9L21 15L12 21Z" fill="#fff"/></svg>
      <div class="abs video-bar"><div class="abs track"><i></i></div></div>
    </div>
    <div class="abs video-tile" style="left:530px">
      <div class="still" role="img" aria-label="Advert video still of a cardboard castle" style="background:linear-gradient(160deg,#7fa8c4,#a9805e 60%,#8b6a4d)"></div>
      <svg class="abs play-btn" viewBox="0 0 30 30" aria-hidden="true"><circle cx="15" cy="15" r="13" fill="rgba(255,255,255,.3)" stroke="#fff" stroke-width="2"/><path d="M12 9L21 15L12 21Z" fill="#fff"/></svg>
      <div class="abs video-bar"><div class="abs track"><i></i></div></div>
    </div>
  </main>

  <footer>
    <svg class="abs footer-scene" viewBox="0 0 840 240" role="img" aria-label="Footer illustration of children standing on grassy hills beside a rainbow">
      <defs>
        <linearGradient id="grass" x1="0" y1="0" x2="0" y2="1">
          <stop offset="0" stop-color="#a9d25a"/>
          <stop offset="1" stop-color="#5f9d2b"/>
        </linearGradient>
      </defs>
      <path d="M0 115C120 92 240 100 360 112C480 124 600 96 720 100C780 102 820 108 840 112V240H0Z" fill="url(#grass)"/>
    </svg>
    <nav class="abs footer-links">
      <a href="#">Home</a><span class="sep">|</span><a href="#">Play Right Now</a><span class="sep">|</span><a href="#">Pictures</a><span class="sep">|</span><a href="#">Get Involved</a><span class="sep">|</span><a href="#">Contact Us</a>
    </nav>
    <p class="abs copyright">©2014 Hop Along Days , All Rights Reserved.</p>
    <div class="abs guild"><span class="guild-mark"></span><span class="guild-name">Northern Games &amp; Crafts Guild</span></div>
  </footer>
</body>
</html>
```